Luxury Business Card Design for High-End Window Treatments

Gilded Slatworks
Custom Plantation Shutters & Architectural Shading Systems

⸻

BACK

Daniel Trevick
Owner

Custom Interior & Exterior Window Treatments

919-555-0148
gildedslatworks.com

I have included a picture that I’m hoping we can use on the back, but I’m also wondering if you can get rid of the ladder? Should we get rid of shutters , shades and blinds underneath Gilded Slatworks?

Target Market(s)

High-end residential homeowners, custom home builders, architects, interior designers, and luxury renovation clients seeking premium plantation shutters and motorized architectural shading systems.

Industry/Entity Type

Custom Window treatments

Contact Information for Business Card

Front Gilded Slatworks Custom Plantation Shutters Motorized Architectural Shading Systems BACK Daniel Trevick Owner 919-555-0148 GildedSlatworks.com Custom Interior & Exterior Window Treatments By Appointment

Requirements
Nice to have
• Not 100% sure on nice to halves or the color but you can definitely check out my website to get a better understanding of what I’m trying to do

```html
<!DOCTYPE html>
<html lang="en">
<head>
<meta charset="utf-8">
<title>Gilded Slatworks – Business Card</title>
<link rel="stylesheet" href="https://fonts.googleapis.com/css2?family=Alegreya:wght@500&family=Raleway:wght@300;500;600&display=swap">
<style>
  :root {
    --canvas: #000000;
    --card: #25282c;
    --gold-dark: #7f5f2c;
    --gold-mid: #a8893f;
    --gold-light: #d8bd6a;
    --gold-text: #b8994c;
    --white: #ffffff;
    --photo-placeholder: #5e6368;
  }
  * { margin: 0; padding: 0; box-sizing: border-box; }
  html, body {
    width: 1200px; height: 1100px; overflow: hidden;
    background: var(--canvas);
  }
  .canvas { position: relative; width: 1200px; height: 1100px; }

  .card {
    position: absolute; left: 273px;
    width: 654px; height: 426px;
    background: var(--card); overflow: hidden;
  }
  .card--front { top: 102px; }
  .card--back { top: 572px; width: 652px; height: 425px; }

  /* Front */
  .side-tab {
    position: absolute; top: 145px; width: 31px; height: 136px;
    background: linear-gradient(180deg, var(--gold-dark) 0%, var(--gold-mid) 50%, var(--gold-light) 51%, var(--gold-dark) 100%);
  }
  .side-tab--left { left: 0; }
  .side-tab--right { right: 0; }

  .front-name {
    position: absolute; left: 0; right: 0; top: 112px;
    text-align: center;
    font-family: "Raleway", sans-serif; font-weight: 300;
    font-size: 76px; line-height: 84px; letter-spacing: 1px;
    color: var(--gold-text);
  }
  .front-services {
    position: absolute; left: 0; right: 0; top: 298px;
    text-align: center; word-spacing: 24px;
    font-family: "Alegreya", serif; font-weight: 500;
    font-size: 31px; line-height: 40px; color: var(--gold-text);
  }

  /* Back */
  .back-art { position: absolute; inset: 0; width: 100%; height: 100%; }

  .back-name {
    position: absolute; right: 28px; top: 44px; text-align: right;
    font-family: "Raleway", sans-serif; font-weight: 300;
    font-size: 37px; line-height: 41px; color: var(--gold-text);
  }
  .contact {
    position: absolute; right: 27px; text-align: right;
    font-family: "Raleway", sans-serif; color: var(--white);
    white-space: nowrap;
  }
  .contact--name { top: 187px; font-size: 32px; line-height: 38px; font-weight: 600; }
  .contact--role { top: 225px; font-size: 17px; line-height: 22px; font-weight: 500; }
  .contact--services { top: 282px; font-size: 20px; line-height: 26px; font-weight: 500; }
  .contact--phone { top: 345px; font-size: 20px; line-height: 26px; font-weight: 300; }
  .contact--web { top: 371px; font-size: 21px; line-height: 26px; font-weight: 300; }
</style>
</head>
<body>
<main class="canvas">

  <section class="card card--front" aria-label="Card front">
    <div class="side-tab side-tab--left"></div>
    <div class="side-tab side-tab--right"></div>
    <h1 class="front-name">Gilded<br>Slatworks</h1>
    <p class="front-services">Shutters Shades Blinds</p>
  </section>

  <section class="card card--back" aria-label="Card back">
    <svg class="back-art" viewBox="0 0 1096 715" preserveAspectRatio="none">
      <defs>
        <linearGradient id="goldBand" x1="0" y1="0" x2="1" y2="0">
          <stop offset="0" stop-color="var(--gold-dark)"/>
          <stop offset="1" stop-color="var(--gold-light)"/>
        </linearGradient>
        <linearGradient id="goldBandReverse" x1="0" y1="0" x2="1" y2="0">
          <stop offset="0" stop-color="var(--gold-light)"/>
          <stop offset="1" stop-color="var(--gold-dark)"/>
        </linearGradient>
      </defs>
      <polygon class="photo-area" role="img" aria-label="Photo of a home with screened porch shades, lawn and patio chairs"
               points="0,222 182,0 852,0 387,569 0,569" fill="var(--photo-placeholder)"/>
      <polygon class="edge-stripe" points="182,0 197,0 0,240 0,222" fill="var(--gold-mid)"/>
      <polygon class="edge-stripe" points="852,0 872,0 287,715 267,715 387,569" fill="var(--gold-mid)"/>
      <polygon class="footer-band" points="0,569 404,569 344,643 0,643" fill="url(#goldBandReverse)"/>
      <polygon class="footer-band" points="0,643 344,643 285,715 0,715" fill="url(#goldBand)"/>
      <polygon class="name-band" points="637,287 1096,287 1096,441 511,441" fill="url(#goldBand)"/>
    </svg>

    <h2 class="back-name">Gilded<br>Slatworks</h2>
    <p class="contact contact--name">Daniel Trevick</p>
    <p class="contact contact--role">Owner</p>
    <p class="contact contact--services">Custom Interior &amp; Exterior<br>Window Treatments</p>
    <p class="contact contact--phone">919-555-0148</p>
    <p class="contact contact--web">gildedslatworks.com</p>
  </section>

</main>
</body>
</html>
```